e-commerce store for sport clothing online store "baseball merchandise "web application...

I want to design a UX/UI for my web application website for the online store I will provide you with the following:
1. screen shots of the initial design for the pages>
2. the logo files.
3. The brand guideline file.

the provided files (screen shots) is guideline I want to see CREATIVITY with the UX/UI DESIGN.
PS. PLEASE FOLLOW THE BRANDGUIDE LINE CAREFULLY SPECIALLY THE TYPOGRAPHY & THE COLOR CODES.

PLEASE VISIT THIS WEBSITE brightlane.varomi-qz.com to see more for the screens.

```html
<!DOCTYPE html>
<html lang="en">
<head>
<meta charset="UTF-8">
<title>Shopping Cart</title>
<link href="https://fonts.googleapis.com/css2?family=Titillium+Web:wght@400;600;700&display=swap" rel="stylesheet">
<style>
  :root {
    --navy: #13254a;
    --crimson: #b3173b;
    --ink: #111111;
    --text: #1d1d1f;
    --line: #9a9a9a;
    --card-border: #d9d9d9;
    --bg: #ffffff;
    --checkout: #000000;
    --trunks: #5fae8a;
    --cap: #c3c7ce;
  }
  * { box-sizing: border-box; margin: 0; padding: 0; }
  html, body { width: 1200px; height: 2667px; overflow: hidden; background: var(--bg); }
  body { font-family: "Titillium Web", sans-serif; color: var(--text); }
  .screen {
    position: relative; width: 360px; height: 800px;
    transform: scale(3.33334); transform-origin: 0 0; background: var(--bg);
  }
  .app-bar {
    position: absolute; left: 0; top: 0; width: 360px; height: 82px; background: var(--navy);
  }
  .app-bar .back { position: absolute; left: 22px; top: 31px; }
  .app-bar h1 {
    position: absolute; left: 0; right: 0; top: 28px; text-align: center;
    color: #fff; font-size: 17px; font-weight: 700; letter-spacing: 0.2px;
  }
  .cart-item {
    position: absolute; left: 8px; width: 344px; height: 125px;
    border: 1px solid var(--card-border); border-radius: 6px; background: #fff;
    box-shadow: 0 2px 5px rgba(0,0,0,0.12); overflow: hidden;
  }
  .cart-item.first { top: 120px; }
  .cart-item.second { top: 260px; }
  .item-photo {
    position: absolute; left: 19px; top: 18px; width: 90px; height: 85px;
    border-radius: 5px; box-shadow: 0 1px 4px rgba(0,0,0,0.2);
  }
  .item-photo.trunks { background: linear-gradient(135deg, #7cc39f, var(--trunks) 60%, #e9d9c5); }
  .item-photo.cap { background: radial-gradient(circle at 50% 50%, var(--cap) 40%, #f4f4f4 70%); }
  .item-name {
    position: absolute; left: 125px; top: 20px; width: 150px;
    font-size: 14px; font-weight: 700; line-height: 18px; color: var(--ink);
  }
  .qty { position: absolute; left: 125px; top: 76px; display: flex; align-items: center; gap: 5px; }
  .qty .value {
    width: 20px; height: 18px; border: 1px solid var(--line); font-size: 13px;
    display: flex; align-items: center; justify-content: center; line-height: 1;
  }
  .item-price {
    position: absolute; right: 11px; bottom: 10px;
    font-size: 15px; font-weight: 700; color: var(--navy);
  }
  .remove {
    position: absolute; right: 0; top: 0; width: 32px; height: 35px;
    background: var(--crimson); border-bottom-left-radius: 8px;
    display: flex; align-items: center; justify-content: center;
  }
  .voucher {
    position: absolute; left: 13px; top: 413px; width: 247px; height: 35px;
    border: 1px solid var(--line); border-radius: 4px;
    font-size: 12px; padding-left: 11px; display: flex; align-items: center; color: var(--ink);
  }
  .apply {
    position: absolute; left: 274px; top: 413px; width: 79px; height: 35px;
    background: var(--navy); border-radius: 6px; color: #fff;
    font-size: 15px; font-weight: 600; display: flex; align-items: center; justify-content: center;
  }
  .summary { position: absolute; left: 11px; top: 475px; width: 320px; }
  .summary .row {
    display: flex; justify-content: space-between; height: 27px; align-items: center;
    font-size: 13px; color: var(--ink);
  }
  .summary .row span:last-child { font-weight: 600; color: var(--navy); }
  .checkout-bar {
    position: absolute; left: 0; top: 742px; width: 360px; height: 58px; background: #fff;
    border-radius: 8px 8px 0 0; box-shadow: 0 -2px 6px rgba(0,0,0,0.15);
  }
  .checkout {
    position: absolute; left: 12px; top: 7px; width: 336px; height: 44px;
    background: var(--checkout); border-radius: 6px; color: #fff;
    font-size: 14px; font-weight: 700; display: flex; align-items: center; justify-content: center;
  }
</style>
</head>
<body>
<main class="screen">
  <header class="app-bar">
    <svg class="back" width="20" height="20" viewBox="0 0 20 20" aria-label="Back">
      <path d="M17 10H4M10 3.5L3.5 10 10 16.5" fill="none" stroke="#fff" stroke-width="2.2" stroke-linecap="round" stroke-linejoin="round"/>
    </svg>
    <h1>Shopping&nbsp; Cart</h1>
  </header>

  <article class="cart-item first">
    <div class="item-photo trunks" role="img" aria-label="Photo of kids green patterned swim trunks"></div>
    <h2 class="item-name">Ripplo Kids Swim Trunks</h2>
    <div class="qty">
      <svg width="17" height="17" viewBox="0 0 17 17"><circle cx="8.5" cy="8.5" r="7.5" fill="none" stroke="#111" stroke-width="1.5"/><path d="M5 8.5h7" stroke="#111" stroke-width="1.8"/></svg>
      <span class="value">1</span>
      <svg width="17" height="17" viewBox="0 0 17 17"><circle cx="8.5" cy="8.5" r="8.5" fill="#13254a"/><path d="M5 8.5h7M8.5 5v7" stroke="#fff" stroke-width="1.8"/></svg>
    </div>
    <p class="item-price">23.000 KD</p>
    <div class="remove">
      <svg width="15" height="16" viewBox="0 0 15 16" aria-label="Remove item"><path d="M1 3.5h13M5 3.5V1.5h5v2M2.8 3.5l.9 11h7.6l.9-11M6 6.5v5.5M9 6.5v5.5" fill="none" stroke="#fff" stroke-width="1.5" stroke-linejoin="round"/></svg>
    </div>
  </article>

  <article class="cart-item second">
    <div class="item-photo cap" role="img" aria-label="Photo of a grey trucker cap"></div>
    <h2 class="item-name">Bass Trucker Cap</h2>
    <div class="qty">
      <svg width="17" height="17" viewBox="0 0 17 17"><circle cx="8.5" cy="8.5" r="7.5" fill="none" stroke="#111" stroke-width="1.5"/><path d="M5 8.5h7" stroke="#111" stroke-width="1.8"/></svg>
      <span class="value">2</span>
      <svg width="17" height="17" viewBox="0 0 17 17"><circle cx="8.5" cy="8.5" r="8.5" fill="#13254a"/><path d="M5 8.5h7M8.5 5v7" stroke="#fff" stroke-width="1.8"/></svg>
    </div>
    <p class="item-price">13.000 KD</p>
    <div class="remove">
      <svg width="15" height="16" viewBox="0 0 15 16" aria-label="Remove item"><path d="M1 3.5h13M5 3.5V1.5h5v2M2.8 3.5l.9 11h7.6l.9-11M6 6.5v5.5M9 6.5v5.5" fill="none" stroke="#fff" stroke-width="1.5" stroke-linejoin="round"/></svg>
    </div>
  </article>

  <div class="voucher">Enter Voucher Code</div>
  <div class="apply">Apply</div>

  <section class="summary">
    <div class="row"><span>Subtotal</span><span>49.000 KD</span></div>
    <div class="row"><span>Delivery Charge</span><span>1.000 KD</span></div>
    <div class="row"><span>Total</span><span>50.000 KD</span></div>
  </section>

  <footer class="checkout-bar">
    <div class="checkout">Go to Checkout</div>
  </footer>
</main>
</body>
</html>
```